Business card for my new company (Accounting firm)

I need a business card for my new business Brightwell Advisory and Ledger SA. Our services are accounting, tax, audit and financial management. Our customers are small companies, start-ups and new companies. The final design has to show financial security, trust and growth. Please find our logo attached to the business card. Text for the business card: Brightwell Advisory and Ledger SA Tomas Varenholt Director and Founder Certified Accountant Tel. 022 418 57 34 tv@clairevalconseil.ch www.clairevalconseil.ch Rue des Vergières 27 1201 Geneva
Target Market(s)
Our customers are small companies, start-ups and new companies.
Industry/Entity Type
Finance And Accounting
Contact Information for Business Card
Claireval Conseil et Comptes SA
Tomas Varenholt
Directeur et Fondateur
Expert-comptable diplômé
Tél. 022 418 57 34
tv@clairevalconseil.ch
www.clairevalconseil.ch
Rue des Vergières 27
1201 Genève

```html
<!DOCTYPE html>
<html lang="fr">
<head>
<meta charset="utf-8">
<title>Claireval Conseil et Comptes SA – Carte de visite</title>
<link rel="stylesheet" href="https://fonts.googleapis.com/css2?family=Roboto:wght@400;500;700&display=swap">
<style>
  :root {
    --backdrop: #e3e4e6;
    --paper: #ffffff;
    --paper-soft: #f1f2f3;
    --blue: #1a76b1;
    --blue-deep: #155f93;
    --blue-light: #2a9ad6;
    --charcoal: #3a3c40;
    --ink-light: #eaf3fa;
    --ink-muted: #cfe3f1;
  }
  * { box-sizing: border-box; margin: 0; padding: 0; }
  html, body {
    width: 1200px; height: 726px; overflow: hidden;
    background: var(--backdrop);
    font-family: "Roboto", Arial, sans-serif;
  }
  .sheet {
    position: relative; width: 1200px; height: 726px;
    display: flex; align-items: center; justify-content: center; gap: 40px;
  }
  .card {
    position: relative; width: 520px; height: 336px;
    background: var(--paper);
    box-shadow: 0 10px 28px rgba(0,0,0,.14), 0 2px 5px rgba(0,0,0,.08);
    overflow: hidden;
  }
  /* front */
  .card-front .accent-stripe {
    position: absolute; left: 0; right: 0; bottom: 34px; height: 7px;
    background: var(--blue);
  }
  .brand {
    position: absolute; display: flex; align-items: center; gap: 12px;
    color: var(--charcoal); font-weight: 500; line-height: 1.15;
  }
  .brand-mark { width: 16px; height: 16px; background: var(--blue); flex: none; }
  .card-front .brand { left: 50%; top: 50%; transform: translate(-50%, -62%); font-size: 26px; }
  .brand-name span { display: block; }
  /* back */
  .card-back .back-art { position: absolute; inset: 0; }
  .card-back .brand { left: 318px; top: 118px; font-size: 19px; }
  .card-back .brand-mark { width: 12px; height: 12px; }
  .holder {
    position: absolute; left: 32px; top: 62px; color: var(--ink-light);
  }
  .holder-name { font-size: 21px; font-weight: 700; margin-bottom: 6px; }
  .holder-role { font-size: 12.5px; line-height: 1.35; color: var(--ink-muted); }
  .contact {
    position: absolute; left: 32px; top: 200px; color: var(--ink-light);
    font-size: 13px; line-height: 1.45; list-style: none;
  }
  .contact li { display: flex; align-items: center; gap: 10px; }
  .contact .icon { width: 14px; height: 14px; flex: none; fill: var(--ink-light); }
  .contact .no-icon { padding-left: 0; }
</style>
</head>
<body>
<main class="sheet">
  <section class="card card-front" aria-label="Recto">
    <div class="brand">
      <span class="brand-mark"></span>
      <span class="brand-name"><span>Claireval</span><span>Conseil et Comptes</span></span>
    </div>
    <div class="accent-stripe"></div>
  </section>

  <section class="card card-back" aria-label="Verso">
    <svg class="back-art" viewBox="0 0 520 336" preserveAspectRatio="none" aria-hidden="true">
      <defs>
        <linearGradient id="backBlue" x1="0" y1="0" x2="1" y2="1">
          <stop offset="0" stop-color="#1f80bb"/>
          <stop offset="1" stop-color="#155f93"/>
        </linearGradient>
      </defs>
      <rect width="520" height="336" fill="url(#backBlue)"/>
      <path d="M306 0 C 300 120, 340 250, 470 336 L 520 336 L 520 0 Z" fill="#3a3c40"/>
      <path d="M318 0 C 312 118, 352 246, 484 336 L 520 336 L 520 0 Z" fill="#f1f2f3"/>
    </svg>

    <div class="brand">
      <span class="brand-mark"></span>
      <span class="brand-name"><span>Claireval</span><span>Conseil et Comptes</span></span>
    </div>

    <div class="holder">
      <p class="holder-name">Tomas Varenholt</p>
      <p class="holder-role">Directeur et Fondateur<br>Expert-comptable diplômé</p>
    </div>

    <ul class="contact">
      <li>Rue des Vergières 27</li>
      <li>1201 Genève</li>
      <li><svg class="icon" viewBox="0 0 24 24"><path d="M6.6 10.8a15.1 15.1 0 0 0 6.6 6.6l2.2-2.2c.3-.3.7-.4 1-.2 1.1.4 2.3.6 3.6.6.6 0 1 .4 1 1V20c0 .6-.4 1-1 1A17 17 0 0 1 3 4c0-.6.4-1 1-1h3.5c.6 0 1 .4 1 1 0 1.3.2 2.5.6 3.6.1.3 0 .7-.2 1z"/></svg>022 418 57 34</li>
      <li><svg class="icon" viewBox="0 0 24 24"><path d="M2 5h20v14H2zm2 2v.5l8 5 8-5V7zm0 2.8V17h16V9.8l-8 5z"/></svg>tv@clairevalconseil.ch</li>
      <li><svg class="icon" viewBox="0 0 24 24"><path d="M12 2a10 10 0 1 0 0 20 10 10 0 0 0 0-20zm6.9 6h-3a15 15 0 0 0-1.3-3.9A8 8 0 0 1 18.9 8zM12 4c.8 1.2 1.5 2.5 1.9 4h-3.8c.4-1.5 1.1-2.8 1.9-4zM4.3 14a8 8 0 0 1 0-4h3.4a16 16 0 0 0 0 4zm.8 2h3a15 15 0 0 0 1.3 3.9A8 8 0 0 1 5.1 16zm3-8h-3a8 8 0 0 1 4.3-3.9C8.8 5.3 8.4 6.6 8.1 8zM12 20c-.8-1.2-1.5-2.5-1.9-4h3.8c-.4 1.5-1.1 2.8-1.9 4zm2.3-6H9.7a14 14 0 0 1 0-4h4.6a14 14 0 0 1 0 4zm.3 5.9c.6-1.2 1-2.5 1.3-3.9h3a8 8 0 0 1-4.3 3.9zm1.7-5.9a16 16 0 0 0 0-4h3.4a8 8 0 0 1 0 4z"/></svg>www.clairevalconseil.ch</li>
    </ul>
  </section>
</main>
</body>
</html>
```